Market Research firm needs updated business cards with new logo

We need the logo to be included somewhere on the card (attached). We would also like the phrases "Independent, Objective, Comprehensive" and "Insight You Can Rely On" somewhere on the card. Front or back. Our colors are hex codes 6075a7, e48d25 and 5a5b5b. Though you are certainly not limited to those shades, whatever you produce should coordinate with them. I have also attached our favicon. Feel free to use it in your design, but please do not use it to replace the full logo.

Contact Information for Business Card

see project description

Font styles to use
Other font styles liked:
• Open Sans

Requirements
Must have
• the logo
• We use Open Sans font

```html
<!DOCTYPE html>
<html lang="en">
<head>
<meta charset="utf-8">
<title>NKV Research — Business Card</title>
<link rel="stylesheet" href="https://fonts.googleapis.com/css2?family=Open+Sans:wght@700;800&family=Roboto+Condensed:wght@400;700&display=swap">
<style>
  :root {
    --slate: #5a5b5b;
    --amber: #e48d25;
    --steel-blue: #6075a7;
    --paper: #ffffff;
    --stage: #000000;
    --ghost: #d6d6d6;
  }
  * { margin: 0; padding: 0; box-sizing: border-box; }
  html, body { width: 1200px; height: 1200px; overflow: hidden; background: var(--stage); }
  .canvas { position: relative; width: 1200px; height: 1200px; }

  .card {
    position: absolute; left: 180px; width: 840px; height: 480px;
    background: var(--paper); overflow: hidden;
  }
  .card--front { top: 90px; }
  .card--back { top: 629px; }
  .card__shape { position: absolute; inset: 0; width: 840px; height: 480px; }

  .wordmark {
    position: absolute; color: var(--amber);
    font-family: "Open Sans", sans-serif; font-weight: 700;
    white-space: nowrap; letter-spacing: -0.5px;
  }
  .wordmark--front { left: 22px; top: 62px; font-size: 34px; }
  .wordmark--back { left: 0; right: 0; top: 130px; text-align: center; font-size: 84px; letter-spacing: -1.5px; }

  .person { position: absolute; left: 54px; top: 332px; font-family: "Roboto Condensed", sans-serif; color: var(--amber); }
  .person__name { font-weight: 700; font-size: 26px; line-height: 1; }
  .person__role { font-weight: 400; font-size: 15px; margin-left: 4px; margin-top: 4px; }

  .contact {
    position: absolute; right: 103px; font-family: "Open Sans", sans-serif;
    font-weight: 700; color: var(--steel-blue); font-size: 24px; line-height: 1;
    white-space: nowrap;
  }
  .contact--email { top: 133px; }
  .contact--phone { top: 235px; font-family: "Roboto Condensed", sans-serif; font-size: 27px; }
  .contact--web { top: 313px; }

  .icon-tile {
    position: absolute; left: 765px; width: 56px; height: 61px;
    background: var(--slate); border-radius: 14px;
    display: flex; align-items: center; justify-content: center;
  }
  .icon-tile svg { width: 36px; height: 36px; }

  .address {
    position: absolute; left: 406px; top: 408px;
    font-family: "Roboto Condensed", sans-serif; font-weight: 700;
    color: var(--steel-blue); font-size: 26px; line-height: 31px;
    white-space: nowrap;
  }
  .pin { position: absolute; left: 340px; top: 411px; width: 40px; height: 52px; }

  .tagline {
    position: absolute; left: 124px; width: 604px; top: 256px;
    display: flex; justify-content: space-between;
    font-family: "Open Sans", sans-serif; font-weight: 700;
    font-size: 17px; color: var(--amber); letter-spacing: 0.3px;
    white-space: nowrap;
  }
</style>
</head>
<body>
<main class="canvas">

  <section class="card card--front" aria-label="Business card front">
    <svg class="card__shape" viewBox="0 0 840 480" aria-hidden="true">
      <circle cx="700" cy="230" r="190" fill="var(--ghost)" opacity="0.35"/>
      <path d="M0 0 H342 Q258 240 342 480 H0 Z" fill="var(--slate)"/>
    </svg>

    <div class="wordmark wordmark--front">NKV Research</div>

    <div class="person">
      <div class="person__name">JOHN SMITH</div>
      <div class="person__role">Ceo/Owner</div>
    </div>

    <div class="contact contact--email">youremail@example.com</div>
    <div class="contact contact--phone">555-014-2276</div>
    <div class="contact contact--web">www.yourwebsite.com</div>

    <div class="icon-tile" style="top:108px">
      <svg viewBox="0 0 36 36" fill="none" stroke="#fff" stroke-width="2.2" stroke-linejoin="round">
        <rect x="5" y="9" width="26" height="18" rx="2"/>
        <path d="M5 10 L18 20 L31 10 M5 26 L14 18 M31 26 L22 18"/>
      </svg>
    </div>
    <div class="icon-tile" style="top:195px">
      <svg viewBox="0 0 36 36" fill="none" stroke="#fff" stroke-width="2.4" stroke-linecap="round" stroke-linejoin="round">
        <path d="M10 8 L14 8 L16 14 L13 16 Q15 21 20 23 L22 20 L28 22 L28 26 Q27 29 23 29 Q9 27 7 12 Q7 8 10 8 Z"/>
        <path d="M21 12 Q24 13 24 16 M21 8 Q28 9 28 16 M21 4 Q32 5 32 16"/>
      </svg>
    </div>
    <div class="icon-tile" style="top:287px">
      <svg viewBox="0 0 36 36" fill="none" stroke="#fff" stroke-width="2.2">
        <circle cx="18" cy="18" r="13"/>
        <ellipse cx="18" cy="18" rx="6" ry="13"/>
        <path d="M5 14 H31 M5 22 H31 M18 5 V31"/>
      </svg>
    </div>

    <svg class="pin" viewBox="0 0 40 52" aria-hidden="true">
      <path d="M20 2 C9 2 2 10 2 20 C2 31 20 50 20 50 C20 50 38 31 38 20 C38 10 31 2 20 2 Z" fill="var(--slate)"/>
      <circle cx="20" cy="19" r="8" fill="#fff"/>
    </svg>
    <div class="address">Your location, OR 97201<br>555-014-2276</div>
  </section>

  <section class="card card--back" aria-label="Business card back">
    <svg class="card__shape" viewBox="0 0 840 480" aria-hidden="true">
      <path d="M0 0 H840 V320 Q420 398 0 320 Z" fill="var(--slate)"/>
    </svg>
    <div class="wordmark wordmark--back">NKV Research</div>
    <div class="tagline">
      <span>INDEPENDENT</span>
      <span>COMPREHENSIVE</span>
      <span>INSIGHT YOU CAN RELY ON</span>
    </div>
  </section>

</main>
</body>
</html>
```